Profesional personal website needs design and business card

I need a business card with my professional name as a logo "Dorian Vitality" for my business. I am a Wellness Coach, consultant and trainer. So it should be professional, wellness oriented and modern.

Target Market(s)

Private clients, governments, corporations. Luxury and high market.

Industry/Entity Type

Health And Wellness

Contact Information for Business Card

Dorian Vitality should be the logo

Colors

Designer to choose colors to be used in the design.

Requirements
Must have
• Dorian Vitality
• Name: Tomás Lirandel
• Wellness Coach, Consultant & Trainer.
• Website: www.dorianvitality-example.com
• Phone:
• Spain (+34) 612 480 317
• (USA) +1 (555) 610 4829
Nice to have
• The most important is the design of "Dorian Vitality", as this is going to be my personal brand logo. It should be professional, wellness, high end and actual.
Should not have
• no golds, no baroque style..

```html
<!DOCTYPE html>
<html lang="en">
<head>
<meta charset="utf-8">
<title>Dorian Vitality – Business Card</title>
<link rel="stylesheet" href="https://fonts.googleapis.com/css2?family=Questrial&display=swap">
<style>
  :root {
    --bg: #2f2f2f;
    --green: #6aab0c;
    --green-deep: #5c960a;
    --ink: #3a3a3a;
    --ink-soft: #555555;
    --paper: #ffffff;
    --rule: #d8d8d8;
    --strip: #3c3c3c;
  }
  * { margin: 0; padding: 0; box-sizing: border-box; }
  html, body {
    width: 1200px; height: 866px; overflow: hidden;
    background: var(--bg);
    font-family: "Questrial", "Century Gothic", sans-serif;
  }
  .sheet {
    width: 1200px; height: 866px;
    display: flex; flex-direction: column;
    align-items: center; justify-content: center; gap: 40px;
  }
  .card {
    position: relative;
    width: 660px; height: 377px;
    overflow: hidden;
    box-shadow: 0 6px 18px rgba(0,0,0,0.45);
  }

  /* Front */
  .card-front { background: var(--paper); }
  .brand {
    position: absolute; left: 370px; top: 118px;
    display: flex; align-items: center; gap: 12px;
  }
  .brand-dot {
    width: 22px; height: 22px; border-radius: 50%;
    background: var(--green);
  }
  .brand-name {
    font-size: 32px; color: var(--ink); letter-spacing: 0.5px;
  }
  .contact {
    position: absolute; left: 40px; top: 130px;
    color: var(--ink-soft);
  }
  .person { font-size: 24px; color: var(--ink); margin-bottom: 4px; }
  .person .surname { color: var(--green); }
  .role { font-size: 15px; margin-bottom: 10px; }
  .phone {
    display: flex; align-items: center; gap: 6px;
    font-size: 15px; line-height: 1.45;
  }
  .phone svg { width: 14px; height: 14px; flex: none; }
  .phone .region { color: var(--green); }
  .rule {
    position: absolute; left: 300px; right: 40px; top: 268px;
    height: 1px; background: var(--rule);
  }
  .website {
    position: absolute; right: 40px; top: 290px;
    font-size: 15px; color: var(--ink-soft);
  }
  .website .domain { color: var(--green); }
  .footer-band {
    position: absolute; left: 0; bottom: 0;
    width: 660px; height: 48px;
  }

  /* Back */
  .card-back {
    background: var(--green);
    display: flex; align-items: center; justify-content: center;
  }
  .back-brand {
    font-size: 54px; color: var(--paper); letter-spacing: 1px;
  }
</style>
</head>
<body>
<main class="sheet">
  <section class="card card-front" aria-label="Business card front">
    <div class="brand">
      <span class="brand-dot"></span>
      <span class="brand-name">Dorian Vitality</span>
    </div>

    <div class="contact">
      <p class="person">Tomás <span class="surname">Lirandel</span></p>
      <p class="role">Wellness Coach, Consultant &amp; Trainer</p>
      <p class="phone">
        <svg viewBox="0 0 14 14" aria-hidden="true"><circle cx="7" cy="7" r="6" fill="none" stroke="#6aab0c" stroke-width="1.4"/><path d="M4.6 3.8 L6 5.4 L5.3 6.3 Q6.2 7.9 7.8 8.7 L8.7 8 L10.2 9.4 L9.3 10.4 Q5.4 9.6 3.7 4.7 Z" fill="#6aab0c"/></svg>
        <span>(+34) 612 480 317 <span class="region">(SPAIN)</span></span>
      </p>
      <p class="phone">
        <svg viewBox="0 0 14 14" aria-hidden="true"><circle cx="7" cy="7" r="6" fill="none" stroke="#6aab0c" stroke-width="1.4"/><path d="M4.6 3.8 L6 5.4 L5.3 6.3 Q6.2 7.9 7.8 8.7 L8.7 8 L10.2 9.4 L9.3 10.4 Q5.4 9.6 3.7 4.7 Z" fill="#6aab0c"/></svg>
        <span>+1 (555) 610 4829<span class="region">(USA)</span></span>
      </p>
    </div>

    <div class="rule"></div>
    <p class="website">www.<span class="domain">dorianvitality-example</span>.com</p>

    <svg class="footer-band" viewBox="0 0 660 48" aria-hidden="true">
      <polygon points="0,34 280,34 266,48 0,48" fill="var(--strip)"/>
      <polygon points="290,30 660,18 660,48 270,48" fill="var(--green)"/>
    </svg>
  </section>

  <section class="card card-back" aria-label="Business card back">
    <p class="back-brand">Dorian Vitality</p>
  </section>
</main>
</body>
</html>
```